BrightLedgerMoney(.com) needs website & logo design

We need our website mock-up made into a reality! We are wanting to launch a multifaceted website for all things financial - i.e. blogs, financial wellness information, and a network of redirect links.
We have an existing mock-up, which I will include, but are open to your creative approach!

Industry/Entity Type

Finance

Coding

Coded - Design and coding required

Number of Pages Required

1 page

Requirements
Must have
• Corresponding logo

```html
<!DOCTYPE html>
<html lang="en">
<head>
<meta charset="utf-8">
<title>Bright Ledger Money</title>
<link href="https://fonts.googleapis.com/css2?family=Raleway:wght@500;600&family=Roboto:wght@400;500;700&display=swap" rel="stylesheet">
<style>
:root{
  --purple:#a58bcb;
  --green:#5ac8a8;
  --text:#444a50;
  --muted:#7b8085;
  --lav:#f3f0f9;
  --white:#fff;
}
*{box-sizing:border-box;margin:0;padding:0}
html,body{width:1200px;height:4005px;overflow:hidden}
body{position:relative;font-family:'Roboto',sans-serif;color:var(--text);background:var(--white)}
.abs{position:absolute}
.head{font-family:'Raleway',sans-serif;font-weight:500}
.pur{color:var(--purple)}
.grn{color:var(--green)}
.btn{position:absolute;border:2px solid var(--green);border-radius:30px;background:#fff;color:var(--green);font-size:13px;font-weight:500;display:flex;align-items:center;justify-content:center;box-shadow:0 4px 10px rgba(0,0,0,.12);text-transform:uppercase}
.site-header{position:absolute;left:0;top:0;width:1200px;height:104px;background:#fff}
.brand{position:absolute;left:110px;top:34px;font-family:'Raleway',sans-serif;font-size:27px;font-weight:500}
.nav{position:absolute;left:488px;top:43px;display:flex;gap:24px;font-size:13px;font-weight:500;color:#333}
.nav .on{color:var(--green)}
.hero{position:absolute;left:0;top:104px;width:1200px;height:569px;background:linear-gradient(90deg,#f2f4f3,#e4efec)}
.hero h1{position:absolute;left:110px;top:130px;font-family:'Raleway',sans-serif;font-weight:500;font-size:38px;line-height:46px}
.hero p{position:absolute;left:110px;top:238px;width:450px;font-size:16px;line-height:27px}
.hero h3{position:absolute;left:110px;top:320px;font-family:'Raleway',sans-serif;font-weight:500;font-size:31px;color:var(--green)}
.email{position:absolute;left:110px;top:383px;width:356px;height:46px;border-radius:30px;background:#fff;box-shadow:0 3px 10px rgba(0,0,0,.12);font-size:14px;color:#777;display:flex;align-items:center;padding-left:22px;gap:10px}
.splash{position:absolute;left:660px;top:20px;width:440px;height:549px;background:radial-gradient(ellipse at center,#9cc8e6 0%,#c9e2ef 55%,rgba(228,239,236,0) 75%)}
.band{position:absolute;left:0;top:673px;width:1200px;height:189px;background:var(--purple);display:flex}
.band .item{flex:1;display:flex;flex-direction:column;align-items:center;justify-content:center;gap:14px;color:#fff;font-size:16px;font-weight:700;border-right:1px solid rgba(255,255,255,.25);margin:22px 0}
.band .item:last-child{border:none}
.photo{position:absolute;left:145px;top:1006px;width:429px;height:377px;background:linear-gradient(135deg,#b9c7c4,#e0cfb0 60%,#d8bf98)}
.frame{position:absolute;left:111px;top:1248px;width:167px;height:168px;border:3px solid var(--green);border-top:none;border-right:none}
.frame:after{content:"";position:absolute;right:-3px;bottom:-3px;width:3px;height:35px;background:var(--green)}
.frame:before{content:"";position:absolute;left:-3px;top:0;width:34px;height:3px;background:var(--green)}
.trend h2{position:absolute;left:645px;top:1000px;font-family:'Raleway',sans-serif;font-weight:500;font-size:35px;line-height:43px}
.trend p{position:absolute;left:645px;width:443px;font-size:14px;line-height:26px;color:var(--muted);text-align:justify}
.services{position:absolute;left:0;top:1530px;width:1200px;height:627px;background:var(--lav)}
.sec-title{position:absolute;left:0;width:1200px;text-align:center;font-family:'Raleway',sans-serif;font-weight:500;font-size:40px}
.card{position:absolute;width:308px;height:187px;background:#fff;border:2px solid var(--green);box-shadow:0 3px 8px rgba(0,0,0,.1);display:flex;flex-direction:column;align-items:center;justify-content:center;gap:18px;font-size:16px;font-weight:500;color:var(--purple);text-transform:uppercase}
.card.active{background:var(--green);color:#fff}
.wellness{position:absolute;left:0;top:2157px;width:1200px;height:514px;background:linear-gradient(90deg,#e5e8e1,#eeeeea 45%,#d6dccb 70%,#e8e8e2)}
.hands{position:absolute;left:590px;top:60px;width:560px;height:400px;background:radial-gradient(ellipse at 40% 55%,#b9a07a 0%,#d5bfa6 30%,rgba(230,232,225,0) 70%)}
.circle{position:absolute;left:111px;top:2227px;width:386px;height:386px;border-radius:50%;background:#fff;text-align:center}
.circle h2{margin-top:70px;font-family:'Raleway',sans-serif;font-weight:500;font-size:35px;line-height:43px}
.circle p{margin:22px auto 0;width:330px;font-size:14px;line-height:25px;color:var(--muted)}
.post{position:absolute;background:#fff;box-shadow:0 2px 10px rgba(0,0,0,.1)}
.post .img{position:absolute}
.meta{display:flex;align-items:center;gap:10px;font-size:11px;color:#555}
.meta i{width:24px;height:24px;border-radius:50%;background:var(--purple);display:inline-block}
.post h4{font-size:16px;font-weight:500;line-height:24px;color:#333;text-transform:uppercase}
.post p{font-size:13px;line-height:24px;color:var(--muted)}
.more{font-size:13px;font-weight:500;color:var(--green);text-decoration:underline}
.cta{position:absolute;left:0;top:3404px;width:1200px;height:216px;background:var(--green);color:#fff}
.cta h2{position:absolute;left:111px;top:58px;font-family:'Raleway',sans-serif;font-weight:500;font-size:35px}
.cta p{position:absolute;left:111px;top:116px;width:660px;font-size:14px;line-height:26px}
.foot-h{position:absolute;top:3700px;font-size:17px;font-weight:500;color:var(--purple);text-transform:uppercase}
.links{position:absolute;left:327px;top:3738px;list-style:none;font-size:14px;line-height:39px}
.links li:before{content:"»";color:var(--green);margin-right:26px}
.ci{position:absolute;left:540px;font-size:12px;line-height:18px;color:#555}
.ci b{display:block;font-size:14px;font-weight:500;color:#333;margin-bottom:2px}
.ci svg{position:absolute;left:0;top:2px}
.ci div{margin-left:37px}
.social{position:absolute;top:3814px;width:36px;height:36px;border-radius:50%;border:2px solid var(--green);background:#fff}
.bottom{position:absolute;left:0;top:3950px;width:1200px;height:55px;background:var(--purple);color:#fff;font-size:12px;display:flex;align-items:center;justify-content:center}
</style>
</head>
<body>

<header class="site-header">
  <div class="brand">Bright Ledger <span class="pur">Money</span></div>
  <nav class="nav"><span class="on">HOME</span><span>ABOUT US</span><span>SERVICES</span><span>RESOURCES</span><span>CONTACT US</span></nav>
  <div class="btn" style="left:946px;top:28px;width:142px;height:46px">Get Started</div>
</header>

<section class="hero">
  <div class="splash" role="img" aria-label="Dollar sign formed from splashing water"></div>
  <h1>A Bright Way To<br><span class="pur">Finance Wellness</span></h1>
  <p>Having insight to relevant information is what we bring to you in a clear and easy to digest way.</p>
  <h3>Signup For Free</h3>
  <div class="email"><svg width="14" height="11" viewBox="0 0 14 11"><rect width="14" height="11" rx="1" fill="#777"/><path d="M1 1l6 5 6-5" stroke="#fff" fill="none"/></svg>Your Email</div>
  <div class="btn" style="left:476px;top:383px;width:140px;height:46px">Get Started</div>
</section>

<section class="band">
  <div class="item"><svg width="60" height="60" viewBox="0 0 60 60" fill="none" stroke="#fff" stroke-width="2"><circle cx="30" cy="20" r="12"/><path d="M8 30v18l12 8M52 30v18l-12 8"/></svg>SAVE</div>
  <div class="item"><svg width="60" height="60" viewBox="0 0 60 60" fill="none" stroke="#fff" stroke-width="2"><rect x="12" y="6" width="30" height="44" rx="2"/><circle cx="42" cy="44" r="10"/><path d="M18 16h18M18 24h12"/></svg>BUDGET</div>
  <div class="item"><svg width="60" height="60" viewBox="0 0 60 60" fill="none" stroke="#fff" stroke-width="2"><rect x="18" y="6" width="28" height="48" rx="3"/><rect x="23" y="12" width="18" height="9"/><path d="M23 28h18M23 36h18M23 44h18"/><circle cx="14" cy="46" r="7"/></svg>CALCULATE</div>
  <div class="item"><svg width="60" height="60" viewBox="0 0 60 60" fill="none" stroke="#fff" stroke-width="2"><path d="M8 54h44M14 54V36h8v18M28 54V28h8v18M42 54V20h8v34M12 26l14-10 10 6 14-14"/></svg>TRACK</div>
  <div class="item"><svg width="60" height="60" viewBox="0 0 60 60" fill="none" stroke="#fff" stroke-width="2"><rect x="6" y="8" width="42" height="34" rx="2"/><circle cx="38" cy="38" r="10"/><path d="M45 45l9 9M12 16h14"/></svg>RESEARCH</div>
  <div class="item"><svg width="60" height="60" viewBox="0 0 60 60" fill="none" stroke="#fff" stroke-width="2"><path d="M52 30a22 22 0 1 1-8-17"/><path d="M46 6v8h-8"/><circle cx="30" cy="30" r="12"/></svg>INVEST</div>
</section>

<section class="trend">
  <svg class="abs" style="left:490px;top:972px" width="120" height="120" viewBox="0 0 120 120">
    <g fill="#c9c9c9">
      <circle cx="2" cy="2" r="2"/><circle cx="14" cy="2" r="2"/><circle cx="26" cy="2" r="2"/><circle cx="38" cy="2" r="2"/><circle cx="50" cy="2" r="2"/><circle cx="62" cy="2" r="2"/><circle cx="74" cy="2" r="2"/><circle cx="86" cy="2" r="2"/><circle cx="98" cy="2" r="2"/><circle cx="110" cy="2" r="2"/>
      <circle cx="2" cy="14" r="2"/><circle cx="14" cy="14" r="2"/><circle cx="26" cy="14" r="2"/><circle cx="38" cy="14" r="2"/><circle cx="50" cy="14" r="2"/><circle cx="62" cy="14" r="2"/><circle cx="74" cy="14" r="2"/><circle cx="86" cy="14" r="2"/><circle cx="98" cy="14" r="2"/><circle cx="110" cy="14" r="2"/>
      <circle cx="2" cy="26" r="2"/><circle cx="14" cy="26" r="2"/><circle cx="26" cy="26" r="2"/><circle cx="38" cy="26" r="2"/><circle cx="50" cy="26" r="2"/><circle cx="62" cy="26" r="2"/><circle cx="74" cy="26" r="2"/><circle cx="86" cy="26" r="2"/><circle cx="98" cy="26" r="2"/><circle cx="110" cy="26" r="2"/>
      <circle cx="98" cy="38" r="2"/><circle cx="110" cy="38" r="2"/><circle cx="98" cy="50" r="2"/><circle cx="110" cy="50" r="2"/><circle cx="98" cy="62" r="2"/><circle cx="110" cy="62" r="2"/><circle cx="98" cy="74" r="2"/><circle cx="110" cy="74" r="2"/><circle cx="98" cy="86" r="2"/><circle cx="110" cy="86" r="2"/><circle cx="98" cy="98" r="2"/><circle cx="110" cy="98" r="2"/><circle cx="98" cy="110" r="2"/><circle cx="110" cy="110" r="2"/>
    </g>
  </svg>
  <div class="frame"></div>
  <div class="photo" role="img" aria-label="Man in a sun hat lying on a beach using a tablet"></div>
  <h2>Trending In 2021:<br><span class="pur">Financial Literacy</span></h2>
  <p style="top:1107px">Lorem ipsum dolor sit amet, consectetur adipiscing elit, sed do eiusmod tempor incididunt ut labore et dolore magna aliqua. Ut enim ad minim veniam, quis nostrud exercitation ullamco laboris nisi ut aliquip ex ea irure dolor in reprehea.</p>
  <p style="top:1220px">Consectetur adipiscing elit, sed do eiusmod tempor incididunt ut labore et dolore magnanim ad minim veniam, quis nostrud exerc itation ullamco laboris nisi ut aliquip.</p>
  <div class="btn" style="left:645px;top:1330px;width:139px;height:48px">Learn More</div>
</section>

<section class="services">
  <div class="sec-title" style="top:66px">What <span class="pur">We Do</span></div>
</section>
<div class="card" style="left:111px;top:1684px"><svg width="64" height="64" viewBox="0 0 64 64" fill="none" stroke="var(--green)" stroke-width="2"><circle cx="32" cy="32" r="22" stroke-dasharray="6 3"/><circle cx="32" cy="32" r="14"/></svg>Set Goals</div>
<div class="card active" style="left:446px;top:1684px"><svg width="64" height="64" viewBox="0 0 64 64" fill="none" stroke="#fff" stroke-width="2"><circle cx="34" cy="20" r="10"/><path d="M8 44h14l10 4h14l8-8M8 54h34l14-12"/></svg>Money 101</div>
<div class="card" style="left:781px;top:1684px"><svg width="64" height="64" viewBox="0 0 64 64" fill="none" stroke="var(--green)" stroke-width="2"><rect x="10" y="6" width="36" height="48" rx="2"/><circle cx="40" cy="40" r="11"/><path d="M48 48l10 10M16 16h14"/></svg>Budgeting</div>
<div class="card" style="left:111px;top:1896px"><svg width="64" height="64" viewBox="0 0 64 64" fill="none" stroke="var(--green)" stroke-width="2"><circle cx="34" cy="16" r="10"/><path d="M8 56h48M16 56V38M28 56V30M40 56V38M50 56V28"/></svg>Credit Mindfulness</div>
<div class="card" style="left:446px;top:1896px"><svg width="64" height="64" viewBox="0 0 64 64" fill="none" stroke="var(--green)" stroke-width="2"><rect x="10" y="6" width="28" height="50" rx="2"/><rect x="38" y="24" width="18" height="32"/><circle cx="24" cy="24" r="7"/><path d="M42 32h10M42 40h10M42 48h10"/></svg>Debt Management</div>
<div class="card" style="left:781px;top:1896px"><svg width="64" height="64" viewBox="0 0 64 64" fill="none" stroke="var(--green)" stroke-width="2"><circle cx="32" cy="32" r="22" stroke-dasharray="6 3"/><circle cx="32" cy="32" r="14"/></svg>Retirement Planning</div>

<section class="wellness">
  <div class="hands" role="img" aria-label="Open hands holding coins with a small tree growing from them"></div>
</section>
<div class="circle">
  <h2>Financial<br><span class="pur">Welness 101</span></h2>
  <p>Lorem ipsum dolor sit amet, consectetur adipiscing elit, sed do eiusmod tempor incididunt ut labore et dolore magna aliqua ut enimcoea.</p>
</div>
<div class="btn" style="left:235px;top:2491px;width:139px;height:48px">Learn More</div>

<div class="sec-title" style="top:2758px">Latest <span class="pur">Blog</span></div>

<article class="post" style="left:111px;top:2849px;width:480px;height:444px">
  <div class="img" style="left:9px;top:9px;width:462px;height:282px;background:linear-gradient(135deg,#dfe3e2,#c9cfcd 60%,#b8b4ad)" role="img" aria-label="Person working through paperwork with a calculator"></div>
  <div class="abs" style="left:30px;top:305px">
    <div class="meta"><i></i>01 Mar 2023</div>
    <h4 style="margin-top:14px;width:420px">Lorem ipsum dolor sit amet consectetur adipiscing elit sed do eiusea</h4>
    <div class="more" style="margin-top:12px">READ MORE</div>
  </div>
</article>
<article class="post" style="left:607px;top:2849px;width:481px;height:213px">
  <div class="img" style="left:9px;top:9px;width:197px;height:197px;background:linear-gradient(135deg,#e9e6e2,#c8bfb6)" role="img" aria-label="Woman in glasses taking notes at a desk"></div>
  <div class="abs" style="left:228px;top:22px;width:235px">
    <div class="meta"><i></i>01 Mar 2023</div>
    <h4 style="margin-top:12px">Lorem ipsum dolor sit amet consea</h4>
    <p style="margin-top:6px">Lorem ipsum dolor sit amet consect etur adipiscing elit sedea</p>
    <div class="more" style="margin-top:6px">READ MORE</div>
  </div>
</article>
<article class="post" style="left:607px;top:3081px;width:481px;height:213px">
  <div class="img" style="left:9px;top:9px;width:197px;height:197px;background:linear-gradient(135deg,#b9c9a8,#8c9b72 50%,#b7935e)" role="img" aria-label="Stacks of coins with a small tree growing on top"></div>
  <div class="abs" style="left:228px;top:22px;width:235px">
    <div class="meta"><i></i>01 Mar 2023</div>
    <h4 style="margin-top:12px">Lorem ipsum dolor sit amet consea</h4>
    <p style="margin-top:6px">Lorem ipsum dolor sit amet consect etur adipiscing elit sedea</p>
    <div class="more" style="margin-top:6px">READ MORE</div>
  </div>
</article>

<section class="cta">
  <h2>Have Any Questions?</h2>
  <p>Lorem ipsum dolor sit amet, consectetur adipiscing elit, sed do eiusmod tempor incididunt ut labore et dolore magna aliqua. Ut enim ad minim veniamea.</p>
</section>
<div class="btn" style="left:950px;top:3487px;width:138px;height:46px;border-color:#fff">Learn More</div>

<footer>
  <div class="abs head" style="left:111px;top:3782px;font-size:29px;line-height:33px">Bright Ledger<br><span class="pur">Money</span></div>
  <div class="foot-h" style="left:327px">Quick Links</div>
  <ul class="links"><li>Home</li><li>About Us</li><li>Services</li><li>Resources</li><li>Contact Us</li></ul>
  <div class="foot-h" style="left:540px">Contact Info</div>
  <div class="ci" style="top:3740px"><svg width="12" height="16" viewBox="0 0 12 16"><path d="M6 0a6 6 0 0 0-6 6c0 4 6 10 6 10s6-6 6-10a6 6 0 0 0-6-6z" fill="var(--green)"/><circle cx="6" cy="6" r="2" fill="#fff"/></svg><div><b>ADDRESS:</b>465, Lorum Ipsum Dolore,<br>United States</div></div>
  <div class="ci" style="top:3816px"><svg width="14" height="14" viewBox="0 0 14 14"><path d="M3 0l3 3-2 2c1 2 3 4 5 5l2-2 3 3-2 3C6 14 0 8 0 3z" fill="var(--green)"/></svg><div><b>PHONE:</b>+1 (888) 888 8888</div></div>
  <div class="ci" style="top:3880px"><svg width="15" height="11" viewBox="0 0 15 11"><rect width="15" height="11" rx="1" fill="var(--green)"/><path d="M1 1l6.5 5L14 1" stroke="#fff" fill="none"/></svg><div><b>EMAIL:</b>info@BrightLedgerMoney.com</div></div>
  <div class="foot-h" style="left:804px">Join Newsletter</div>
  <div class="abs" style="left:804px;top:3744px;width:284px;height:46px;border-radius:30px;background:#fff;box-shadow:0 3px 10px rgba(0,0,0,.12);font-size:14px;color:#555;padding:15px 18px">Email Address</div>
  <div class="abs" style="left:980px;top:3747px;width:104px;height:40px;border-radius:30px;background:var(--green);color:#fff;font-size:13px;font-weight:700;display:flex;align-items:center;justify-content:center">JOIN NOW</div>
  <div class="social" style="left:806px;background:var(--green)"></div>
  <div class="social" style="left:850px"></div>
  <div class="social" style="left:893px"></div>
  <div class="bottom">© 2023&nbsp;<span style="font-weight:500">BRIGHT LEDGER MONEY</span>&nbsp;&nbsp;|&nbsp;&nbsp;All Rights Reserved</div>
</footer>

</body>
</html>
```